Workers comp/Business Ins/ Payroll- Postcard

I own an insurance agency.  I'm interested in getting some professional advice on how to design a message for what i want to sell.  The products I want to sell are 1) Workers compensation 2) business Insurance 3) Payroll processing. They are integrated together but I'm not sure if it's too much to put on a postcard and if I don't put it on a postcard I could be missing out on sales.
I have the ability to look up what Insurance company a business has their workers compensation  policy with, along with their expiration date.  Based on that information I can tell if the business is overpaying for their Workers compensation. insurance. Most companies are overpaying so I can usually save a company money very quickly if I can get in front of them. Some businesses work with a broker such as myself and buy a policy. When it's done this way, the business ESTIMATES his payroll for the year and at the end of the year they have to complete an audit to find out the actual payroll. Based on audit, they will either owe more money if they were low or get money back if they were high. The other way a business buys a workers comp. policy is with their payroll company. The payroll company will place the policy on Pay -as- you -go which means when you pay your employees every week they  will also calculate how much the workers comp premium is for the week and take that amount out of their checking account. This method avoids large down payments, helps with cash flow and should be very accurate at the end of the policy term.  This is by far the best way to do this for the businessowner. My company also has payroll company and we do this for the insured as well. However, most payroll company's such as KRV and Wagebrook charge the customer $15 every time they do this so if it's weekly it is another $780 a year.  We also complete the insured's audit for them which is a big headache for the businessowner.
One of our biggest benefits of doing business with our company is we have a  Price lock for Life. When you sign up your base price will never increase. Payroll companies are famous for "discounting a new client" only to increase the rate in a few months later. Our service is also superior to the other payroll companies who use overseas service centers. We have staff within our office and we can answer questions quickly. We usually save businesses money on  their Payroll processing but it's not what we focus on- We focus on the Service.
Business Insurance- One of our main companies that we represent is Tolland Insurance. Tolland is very competitive and we usually write business accounts where we save the business owner money but offer superior coverages.
in summary, I'm offering 1) better workers compensation rates 2) Pay as you go workers comp. 3) Price Lock, audits done for you, and superior customer service with our payroll company 4) savings on their business insurance with superior coverages.
Sometimes when we talk to an insured we may start with just their payroll and later get the WC and business liability. Each account is different and we do not pressure people to make decisions and we do what is right for them.  The biggest takeaway is we take some things off the plate for the businessowner where they can make just one phone call to get what they need done.  Our Website is www.brightmoor-partners.net. my email is tomk@brightmoor-partners.net if you have any questions.
Thank You
Tom Kessler

Target Market(s)
Small business owners 1-50 employees
Industry/Entity Type
Insurance and Payroll
Font styles to use
Other font styles liked:
- Let designer choose

Colors
Designer to choose colors to be used in the design.
Requirements
Must have
- It shouldn't be boring- needs to stand out- can use 6x11 inch postcard

Nice to have
- I like humor but not a must

Should not have
- Nothing I can think of

```html
<!DOCTYPE html>
<html lang="en">
<head>
<meta charset="utf-8">
<title>Brightmoor Partners Insurance – Postcard</title>
<link href="https://fonts.googleapis.com/css2?family=Poppins:wght@400;500;600;700&family=Tinos:wght@700&display=swap" rel="stylesheet">
<style>
:root{
  --stage:#8a8a8a;
  --red-dark:#7e2a30;
  --red:#b1444b;
  --brand:#8a2c33;
  --ink:#111;
  --panel-grey:#dcdcdd;
  --bar-grey:#4e4e4f;
  --bar-black:#0c0c0c;
  --white:#fff;
}
*{margin:0;padding:0;box-sizing:border-box}
html,body{width:1002px;height:1200px;overflow:hidden;background:var(--stage)}
body{position:relative;font-family:"Poppins",Arial,sans-serif;color:var(--ink)}
.card{position:absolute;left:73px;width:855px;height:466px;overflow:hidden;background:var(--white);box-shadow:0 14px 12px -8px rgba(0,0,0,.35)}
.card--front{top:90px}
.card--back{top:642px;height:467px}
.abs{position:absolute;white-space:nowrap}
.shapes{position:absolute;left:0;top:0}
.serif{font-family:"Tinos","Times New Roman",serif;font-weight:700}

/* brand name */
.brand-name{color:var(--brand);font-family:"Tinos","Times New Roman",serif;font-weight:700;text-align:center;line-height:1}
.brand-name .word{display:block;font-size:31px;letter-spacing:.5px}
.brand-name .sub{display:block;font-size:13px;letter-spacing:12px;margin-top:6px;padding-left:12px}

/* front */
.photo-team{position:absolute;left:0;top:0;width:855px;height:401px;
  clip-path:polygon(520px 60px,855px 60px,855px 401px,542px 401px,448px 228px);
  background:linear-gradient(110deg,#3f4d55 0%,#8f7868 28%,#e6ddd2 50%,#d9cfc4 68%,#31515d 100%)}
.tagline-top{right:27px;top:23px;color:var(--white);font-weight:700;font-size:10.5px}
.service{color:var(--white);font-weight:500;font-size:17px}
.tick{position:absolute;width:14px;height:11px}
.headline{left:0;width:498px;text-align:center;font-size:35px;line-height:1}
.headline--red{color:var(--brand)}
.pill{left:99px;top:342px;width:301px;height:37px;background:#000;border-radius:6px;color:var(--white);font-weight:600;font-size:12.5px;display:flex;align-items:center;justify-content:center}
.social{left:417px;top:349px;display:flex;gap:9px}
.social span{width:22px;height:22px;border:2px solid var(--brand);border-radius:50%;display:block}

/* contact bars */
.contact{font-size:11.5px;color:var(--white);display:flex;align-items:center;gap:6px;height:32px}
.contact svg{flex:none}
.contact--call{font-size:12px;gap:5px}
.contact .big{font-size:14.5px;font-weight:500}
.locations{left:0;width:855px;text-align:center;color:var(--white);font-size:12.5px;letter-spacing:.1px}

/* back */
.photo-signing{position:absolute;left:0;top:0;width:855px;height:403px;
  background:linear-gradient(100deg,#e2e2e5 0%,#ececef 35%,#f6f6f8 60%,#f0f0f3 80%,#f9f9fb 100%)}
.lines-of-business{left:106px;top:126px;font-weight:600;font-size:10.5px}
.stamp{left:761px;top:29px;width:65px;height:64px;border:1.5px solid #111;border-radius:6px}
.address-line{left:512px;width:311px;height:1px;background:#222}
.q-head{font-size:29px;line-height:1}
.q-head .red{color:var(--brand)}
.body-copy{font-size:13.2px;line-height:15.5px;white-space:normal}
.banner-text{left:514px;width:290px;top:207px;height:31px;display:flex;align-items:center;justify-content:center;color:var(--white);font-size:12.5px}
.benefit{left:515px;display:flex;align-items:center;gap:10px;font-size:12.5px}
.checkbox{width:11px;height:11px;flex:none}
</style>
</head>
<body>

<!-- FRONT -->
<section class="card card--front">
  <svg class="shapes" width="855" height="466" viewBox="0 0 855 466">
    <defs>
      <linearGradient id="redGrad" x1="0" x2="1">
        <stop offset="0" stop-color="#7e2a30"/><stop offset="1" stop-color="#b3464d"/>
      </linearGradient>
    </defs>
    <rect x="0" y="229" width="855" height="172" fill="#dcdcdd"/>
    <polygon points="0,0 150,0 99,60 0,60" fill="url(#redGrad)"/>
    <polygon points="478,0 855,0 855,60 520,60" fill="url(#redGrad)"/>
    <polygon points="0,149 482,149 447,229 0,229" fill="url(#redGrad)"/>
    <rect x="0" y="401" width="855" height="32" fill="#4e4e4f"/>
    <polygon points="244,401 628,401 617,433 235,433" fill="#b1444b"/>
    <rect x="0" y="433" width="855" height="33" fill="#0c0c0c"/>
  </svg>

  <div class="photo-team" role="img" aria-label="Photo of a small business team gathered around a laptop reviewing documents"></div>

  <p class="abs tagline-top">Get Better Rates • Pay-As-You-Go • Lifetime Price Lock</p>

  <div class="abs brand-name" style="left:70px;width:360px;top:82px">
    <span class="word">BRIGHTMOOR PARTNERS</span>
    <span class="sub">INSURANCE</span>
  </div>

  <svg class="tick" style="left:41px;top:166px" viewBox="0 0 14 11"><path d="M1 6l3 3 5-7M6 8l1 1 6-8" fill="none" stroke="#fff" stroke-width="2"/></svg>
  <p class="abs service" style="left:66px;top:158px">Workers Comp</p>
  <svg class="tick" style="left:230px;top:169px" viewBox="0 0 14 11"><path d="M1 6l3 3 5-7M6 8l1 1 6-8" fill="none" stroke="#fff" stroke-width="2"/></svg>
  <p class="abs service" style="left:254px;top:161px">Business Insurance</p>
  <svg class="tick" style="left:41px;top:197px" viewBox="0 0 14 11"><path d="M1 6l3 3 5-7M6 8l1 1 6-8" fill="none" stroke="#fff" stroke-width="2"/></svg>
  <p class="abs service" style="left:66px;top:189px">Payroll Processing</p>

  <h1 class="abs headline serif" style="top:246px">Cut Costs. Save Time.</h1>
  <h2 class="abs headline headline--red serif" style="top:288px">Simplify Your Business.</h2>

  <p class="abs pill">One Call. One Team. Everything You Need.</p>
  <div class="abs social" aria-label="Social media"><span></span><span></span><span></span></div>

  <p class="abs contact" style="left:20px;top:401px">
    <svg width="13" height="9" viewBox="0 0 14 10"><rect x=".5" y=".5" width="13" height="9" fill="none" stroke="#fff"/><path d="M.5 .5L7 6l6.5-5.5" fill="none" stroke="#fff"/></svg>
    tomk@brightmoor-partners.net
  </p>
  <p class="abs contact contact--call" style="left:256px;top:401px">
    <svg width="11" height="11" viewBox="0 0 12 12"><path d="M2.5 0.5l2 2.5-1.2 1.5c.8 1.7 2.1 3 3.8 3.8l1.5-1.2 2.5 2-1.2 2.4C5 11 1 7 .3 1.7z" fill="#fff"/></svg>
    Call us today - <span class="big">585.555.0142 or (844) 555-0199</span>
  </p>
  <p class="abs contact" style="left:640px;top:401px">
    <svg width="10" height="10" viewBox="0 0 11 11"><path d="M1 1l9 3.5-3.5 1.2 3 3-1.3 1.3-3-3L4 10z" fill="#fff"/></svg>
    www.brightmoor-partners.net
  </p>
  <p class="abs locations" style="top:441px">TWO LOCATIONS&nbsp; : &nbsp;1280 ORCHARD ROAD | MILLBROOK, NY 14471 | 585-555-0142 &nbsp;| &nbsp;22 ELM PLACE | CEDARVALE, NY 14420 | 585-555-0177</p>
</section>

<!-- BACK -->
<section class="card card--back">
  <div class="photo-signing" role="img" aria-label="Soft faded photo of hands signing a contract with a pen"></div>
  <svg class="shapes" width="855" height="467" viewBox="0 0 855 467">
    <defs>
      <linearGradient id="redGrad2" x1="0" x2="1">
        <stop offset="0" stop-color="#7e2a30"/><stop offset="1" stop-color="#b3464d"/>
      </linearGradient>
    </defs>
    <polygon points="0,0 130,0 97,40 0,40" fill="url(#redGrad2)"/>
    <polygon points="514,207 815,207 795,238 514,238" fill="#b1444b"/>
    <rect x="0" y="403" width="855" height="32" fill="#4e4e4f"/>
    <polygon points="244,403 628,403 617,435 235,435" fill="#b1444b"/>
    <rect x="0" y="435" width="855" height="32" fill="#0c0c0c"/>
  </svg>

  <div class="abs brand-name" style="left:24px;width:360px;top:72px">
    <span class="word">BRIGHTMOOR PARTNERS</span>
    <span class="sub">INSURANCE</span>
  </div>
  <p class="abs lines-of-business">AUTO | HOME | BUSINESS | PAYROLL</p>

  <div class="abs stamp"></div>
  <div class="abs address-line" style="top:138px"></div>
  <div class="abs address-line" style="top:181px"></div>

  <svg class="abs" style="left:18px;top:167px" width="24" height="19" viewBox="0 0 24 19"><path d="M2 10l5 5 8-13M10 14l2 2 10-14" fill="none" stroke="#7e2a30" stroke-width="3.5"/></svg>
  <h2 class="abs q-head serif" style="left:46px;top:159px">Are You Overpaying</h2>
  <h2 class="abs q-head serif" style="left:46px;top:191px"><span class="red">for Workers Comp?</span></h2>
  <p class="abs body-copy" style="left:46px;top:221px;width:340px">We can tell you right now who your policy is with and if you're spending too much. Most companies are - and we fix that fast.</p>

  <svg class="abs" style="left:18px;top:303px" width="24" height="19" viewBox="0 0 24 19"><path d="M2 10l5 5 8-13M10 14l2 2 10-14" fill="none" stroke="#7e2a30" stroke-width="3.5"/></svg>
  <h2 class="abs q-head serif" style="left:47px;top:295px">Business <span class="red">Insurance?</span></h2>
  <p class="abs body-copy" style="left:47px;top:324px;width:345px">We work with Tolland Insurance and others to save you money without cutting coverage.</p>

  <p class="abs banner-text serif">Smart Payroll + Workers Comp Integration</p>

  <p class="abs benefit serif" style="top:252px"><svg class="checkbox" viewBox="0 0 11 11"><rect width="11" height="11" fill="#8a2c33"/><path d="M2.5 5.5l2 2 4-4.5" fill="none" stroke="#fff" stroke-width="1.5"/></svg>Pay-As-You-Go -&nbsp; No Big Down Payments</p>
  <p class="abs benefit serif" style="top:273px"><svg class="checkbox" viewBox="0 0 11 11"><rect width="11" height="11" fill="#8a2c33"/><path d="M2.5 5.5l2 2 4-4.5" fill="none" stroke="#fff" stroke-width="1.5"/></svg>Audit Support - We Handle It For You</p>
  <p class="abs benefit serif" style="top:293px"><svg class="checkbox" viewBox="0 0 11 11"><rect width="11" height="11" fill="#8a2c33"/><path d="M2.5 5.5l2 2 4-4.5" fill="none" stroke="#fff" stroke-width="1.5"/></svg>Price Lock for Life - No Surprise Rate Hikes</p>
  <p class="abs benefit serif" style="top:314px"><svg class="checkbox" viewBox="0 0 11 11"><rect width="11" height="11" fill="#8a2c33"/><path d="M2.5 5.5l2 2 4-4.5" fill="none" stroke="#fff" stroke-width="1.5"/></svg>No Extra Fees - Unlike KRV &amp; Wagebrook</p>

  <p class="abs body-copy" style="left:515px;top:338px;width:320px">Bonus: Our U.S.-based team offers real, responsive service —no overseas call centers.</p>
  <p class="abs body-copy" style="left:47px;top:376px;white-space:nowrap">Let’s Make It Easy. Whether you start with payroll, workers comp, or insurance—we’ll handle it. You focus on your business.</p>

  <p class="abs contact" style="left:20px;top:403px">
    <svg width="13" height="9" viewBox="0 0 14 10"><rect x=".5" y=".5" width="13" height="9" fill="none" stroke="#fff"/><path d="M.5 .5L7 6l6.5-5.5" fill="none" stroke="#fff"/></svg>
    tomk@brightmoor-partners.net
  </p>
  <p class="abs contact contact--call" style="left:256px;top:403px">
    <svg width="11" height="11" viewBox="0 0 12 12"><path d="M2.5 0.5l2 2.5-1.2 1.5c.8 1.7 2.1 3 3.8 3.8l1.5-1.2 2.5 2-1.2 2.4C5 11 1 7 .3 1.7z" fill="#fff"/></svg>
    Call us today - <span class="big">585.555.0142 or (844) 555-0199</span>
  </p>
  <p class="abs contact" style="left:640px;top:403px">
    <svg width="10" height="10" viewBox="0 0 11 11"><path d="M1 1l9 3.5-3.5 1.2 3 3-1.3 1.3-3-3L4 10z" fill="#fff"/></svg>
    www.brightmoor-partners.net
  </p>
  <p class="abs locations" style="top:443px">TWO LOCATIONS&nbsp; : &nbsp;1280 ORCHARD ROAD | MILLBROOK, NY 14471 | 585-555-0142 &nbsp;| &nbsp;22 ELM PLACE | CEDARVALE, NY 14420 | 585-555-0177</p>
</section>

</body>
</html>
```